Brightway Haul & Upkeep Services, are a company that offers a 'one stop shop' pre-move clean up a

I have already selected a logo which I would like on the front of the business cards along with phone numbers, web address and email which are:
0487650392
www.brightwayhaul.com.au
brightwayhaulandupkeep@mailbox.example

On the back of the card I would like to list some of the types of service we offer (clean - move - repairs/maintenance) which are:
CLEAN - windows, gutters, solar panels, driveways/paths, carpets.
MOVE - Small/medium size house/office moves, large item pick-up & delivery, yard clean-up and removal.
General maintenance and repairs.

I would like the blue logo on a gray background.

Thanks

```html
<!DOCTYPE html>
<html lang="en">
<head>
<meta charset="utf-8">
<title>Brightway Haul &amp; Upkeep Services – Business Cards</title>
<link href="https://fonts.googleapis.com/css2?family=Open+Sans:wght@400;600;700;800&display=swap" rel="stylesheet">
<style>
  :root {
    --backdrop: #5e3a2a;
    --card-light: #f1f2f3;
    --card-mid: #d6d8da;
    --card-dark: #b9bcbf;
    --brand-blue: #2f7fc8;
    --ink: #2a2a2a;
    --ink-soft: #3c3c3c;
  }
  * { box-sizing: border-box; margin: 0; padding: 0; }
  html, body {
    width: 1200px; height: 682px; overflow: hidden;
    background: var(--backdrop);
    font-family: "Open Sans", Arial, sans-serif;
  }
  .sheet {
    width: 1200px; height: 682px;
    display: flex; align-items: center; justify-content: center; gap: 50px;
  }
  .card {
    position: relative;
    width: 540px; height: 320px;
    overflow: hidden;
    background: radial-gradient(ellipse at 40% 35%, var(--card-light) 0%, var(--card-mid) 65%, var(--card-dark) 100%);
    box-shadow: 0 10px 24px rgba(0,0,0,0.45);
  }

  /* Brand name block */
  .brand {
    display: flex; align-items: center; gap: 12px;
    color: var(--brand-blue);
    font-weight: 800;
    line-height: 1.05;
  }
  .brand-mark {
    flex: none;
    width: 22px; height: 22px;
    background: var(--brand-blue);
  }

  /* Front */
  .card-front .brand {
    position: absolute; left: 44px; top: 62px;
    font-size: 30px; width: 440px;
  }
  .card-front .website {
    position: absolute; left: 54px; top: 238px;
    font-size: 12px; letter-spacing: 2px; color: var(--ink);
    white-space: nowrap;
  }
  .card-front .divider {
    position: absolute; left: 288px; top: 178px;
    width: 1.5px; height: 112px; background: var(--brand-blue);
  }
  .contact-list {
    position: absolute; left: 300px; top: 188px;
    list-style: none;
    font-size: 12.5px; color: var(--ink);
  }
  .contact-list li { display: flex; align-items: center; gap: 7px; margin-bottom: 14px; white-space: nowrap; }
  .contact-list .email { font-size: 9.5px; }
  .contact-list svg { width: 11px; height: 11px; flex: none; fill: var(--brand-blue); }

  /* Back */
  .card-back .brand {
    position: absolute; left: 60px; top: 54px;
    font-size: 32px; width: 440px;
  }
  .services-title {
    position: absolute; left: 0; right: 0; top: 178px;
    text-align: center;
    font-size: 20px; font-weight: 700; letter-spacing: 6px;
    color: var(--brand-blue);
  }
  .services-list {
    position: absolute; left: 0; right: 0; top: 222px;
    list-style: none; text-align: center;
    font-size: 17px; font-weight: 600; color: var(--ink-soft);
    line-height: 1.45;
  }
  .services-list .pair span + span { margin-left: 18px; }
</style>
</head>
<body>
<main class="sheet">

  <section class="card card-front" aria-label="Card front">
    <div class="brand"><span class="brand-mark"></span><span>Brightway Haul &amp; Upkeep Services</span></div>
    <p class="website">www.brightwayhaul.com.au</p>
    <div class="divider"></div>
    <ul class="contact-list">
      <li>
        <svg viewBox="0 0 24 24" aria-hidden="true"><path d="M6.6 10.8a15.1 15.1 0 0 0 6.6 6.6l2.2-2.2a1 1 0 0 1 1-.25 11.4 11.4 0 0 0 3.6.57 1 1 0 0 1 1 1V20a1 1 0 0 1-1 1A17 17 0 0 1 3 4a1 1 0 0 1 1-1h3.5a1 1 0 0 1 1 1c0 1.25.2 2.45.57 3.57a1 1 0 0 1-.25 1z"/></svg>
        <span>0487650392</span>
      </li>
      <li class="email">
        <svg viewBox="0 0 24 24" aria-hidden="true"><path d="M2 5h20v14H2z M4 7v.4l8 5 8-5V7l-8 5z" fill-rule="evenodd"/></svg>
        <span>brightwayhaulandupkeep@mailbox.example</span>
      </li>
    </ul>
  </section>

  <section class="card card-back" aria-label="Card back">
    <div class="brand"><span class="brand-mark"></span><span>Brightway Haul &amp; Upkeep Services</span></div>
    <h2 class="services-title">Services we offer</h2>
    <ul class="services-list">
      <li class="pair"><span>• Clean</span><span>• Move</span></li>
      <li>• General maintenance and repairs.</li>
    </ul>
  </section>

</main>
</body>
</html>
```